Create a Wordpress Design (Dorrel)

We need a wordpress design for an established auction and real estate company based in Tennessee. The winning design will incorporate a professional color scheme with company logo in a clean layout. The design needs to consider that this will be developed on a responsive theme. Colors are those that will highlight the logo.
Updates

This client, an older gentleman, wants the site to mimic http://www.quillfordbidhouse.example/. If you can adjust you designs with this site in mind - perhaps 3 columns, less color etc. We are trying to get him a concept that he likes and he keeps mentioning this site. Do not copy this site, but keep it in mind while re-doing the concept. Thanks, - auction services -

Industry/Entity Type

Real Estate

Font styles to use
Sans Serif

Colors

Designer to choose colors to be used in the design.

Requirements
Must have
• - Navigation: 1) Home - with auctions as content as seen at http://brenwickgavel.example/ 2) Properties for Sale 3) Auctions 4) Sell Your Property 5) Community Info 6) About Us 7) Contact Us

Color will be those that highlight logo in a professional creative way. Site tagline: "Our Signs are Everywhere". Site will have a slideshow - please use stock real estate image for the initial photo.

Widgets: 1) social media (FB twitter, linked In, Youtube, RSS) 2) News & Events blog, 3) testimonials 4) featured Property widget.

Footer will have contact info (below) smaller company logo, and the association logos attached, and contact info:
Phone: (615) 555-0178
Contacts: Marion Teague-Hollis
Email: marketing@kenwoodorrel.example
Address: 22-C Elmfield Court W, Murfreesboro, TN 37199

Nice to have
• use and styling of a dropdown menu: Under AUCTIONS, 1) Upcoming 2) Past

```html
<!DOCTYPE html>
<html lang="en">
<head>
<meta charset="utf-8">
<title>Dorrel Commercial — Realtors &amp; Auctioneers</title>
<link href="https://fonts.googleapis.com/css2?family=Roboto:wght@300;400;500&family=Open+Sans:wght@400;600&display=swap" rel="stylesheet">
<style>
:root{
  --red:#c3161c;
  --red-dark:#a80f15;
  --ink:#2a2a2a;
  --text:#444;
  --muted:#6b6b6b;
  --line:#d9d9d9;
  --nav-dark:#3a3a3a;
  --footer-grey:#f2f2f2;
  --black:#0b0b0b;
}
*{box-sizing:border-box;margin:0;padding:0}
html,body{width:762px;height:1200px;overflow:hidden;background:#fff}
body{position:relative;font-family:"Roboto",sans-serif;color:var(--text)}
.abs{position:absolute}

/* header */
.brand{left:62px;top:20px;height:46px;display:flex;align-items:center;gap:8px}
.brand-mark{width:14px;height:14px;border-radius:50%;background:var(--red)}
.brand-name{font-size:24px;font-weight:500;color:var(--red);letter-spacing:.5px}
.phone{left:455px;top:41px;display:flex;align-items:center;gap:7px;font-size:12.5px;color:var(--ink)}
.phone-icon{width:15px;height:15px;border-radius:3px;background:var(--red);display:flex;align-items:center;justify-content:center}
.search{left:563px;top:37px;width:134px;height:25px;background:#f3f3f3;border:1px solid #e2e2e2;font-size:7.5px;color:#333;padding:8px 9px}
.search svg{position:absolute;right:8px;top:6px}

/* nav */
.nav{left:62px;top:82px;width:636px;height:36px;background:var(--red);display:flex;font-size:9.5px;color:#fff;text-transform:uppercase}
.nav-item{position:absolute;top:0;height:36px;line-height:38px;white-space:nowrap}
.nav-item.home{left:0;width:56px;background:var(--nav-dark);padding-left:12px}
.nav-sep{position:absolute;top:0;width:1px;height:36px;background:rgba(0,0,0,.15)}
.dropdown{left:232px;top:118px;width:76px;height:39px;background:var(--red);box-shadow:0 2px 3px rgba(0,0,0,.3);font-size:8px;color:#fff;padding:5px 0 0 19px;line-height:17.5px}

/* hero */
.hero{left:62px;top:118px;width:636px;height:269px;background:linear-gradient(180deg,#8fb4dc 0%,#cfd8d6 35%,#d9d6c8 55%,#6f8f4a 80%,#3f6a2a 100%)}
.hero-caption{left:355px;top:239px;width:343px;height:58px;background:rgba(30,30,30,.72);color:#fff;font-size:14.5px;line-height:24px;padding:5px 0 0 17px}
.hero-dots{left:647px;top:305px;display:flex;gap:4px}
.hero-dots span{width:9px;height:9px;border-radius:50%;background:#fff}
.hero-dots span.on{background:var(--red)}

/* featured */
.featured{left:62px;top:397px;width:636px;height:168px;border:1px solid var(--line);border-radius:3px;box-shadow:0 1px 2px rgba(0,0,0,.1)}
.section-title-red{left:74px;top:409px;font-size:15.5px;color:var(--red)}
.feat-dots{left:658px;top:416px;display:flex;gap:3px}
.feat-dots span{width:5px;height:5px;border-radius:50%;background:#333}
.feat-dots span.on{background:var(--red)}
.feat-photo{top:438px;width:142px;height:80px;border-radius:2px}
.feat-caption{top:528px;font-family:"Open Sans",sans-serif;font-size:11px;color:#222}

/* auctions */
.section-title{font-size:14.5px;color:#222;font-weight:400}
.arrows{left:438px;top:586px;display:flex;gap:2px}
.arrows span{width:13px;height:13px;background:#555;display:flex;align-items:center;justify-content:center}
.auction-card{left:64px;width:401px;height:139px;border:1px solid var(--line);border-radius:2px;box-shadow:0 1px 2px rgba(0,0,0,.12)}
.auction-photo{left:12px;top:10px;width:143px;height:115px}
.auction-title{left:171px;top:10px;font-size:13px;color:var(--red);font-weight:400}
.auction-lines{left:171px;top:31px;font-size:9.3px;line-height:14.6px;color:#333}
.btn-details{left:170px;top:104px;width:67px;height:21px;background:var(--red);color:#fff;font-size:10px;text-align:center;line-height:21px;border-radius:2px}

/* news */
.news-photo{left:482px;width:64px;height:48px}
.news-text{left:552px;width:148px;font-size:7.6px;line-height:11.5px;color:#555;letter-spacing:.2px}
.news-date{font-size:7.6px;color:var(--red);letter-spacing:.3px;margin-top:4px}
.news-sep{left:482px;width:215px;border-top:1px dotted #999}

/* footer */
.footer-band{left:0;top:938px;width:762px;height:114px;background:var(--footer-grey)}
.footer-head{top:951px;font-size:9.5px;color:var(--red)}
.contact-lines{left:64px;top:973px;font-size:7.3px;line-height:11.5px;color:#555}
.testimonial{left:245px;top:973px;width:256px;height:69px;background:#fff}
.avatar{left:9px;top:6px;width:53px;height:53px;border-radius:50%;background:radial-gradient(circle,#d8c3ad,#a88a70)}
.quote{left:75px;top:13px;width:170px;font-size:7.6px;line-height:13.5px;color:#666}
.quote b{color:var(--red);font-weight:400}
.newsletter{left:546px;top:977px;width:143px;height:24px;background:#fff;border:1px solid #ccc;font-size:7.5px;font-style:italic;color:#777;padding:7px 7px}
.go{right:-1px;top:-1px;width:23px;height:24px;background:#333;color:#fff;font-size:8px;font-style:normal;text-align:center;line-height:24px}
.social{left:547px;top:1017px;display:flex;gap:6px}
.social span{width:24px;height:24px;border-radius:50%;border:2px solid #999}
.badges-band{left:0;top:1052px;width:762px;height:68px;background:linear-gradient(180deg,#fff 0%,#e6e6e6 100%)}
.badges{left:200px;top:1075px;display:flex;gap:9px;align-items:center}
.badge{background:#3a3a3a;height:35px}
.copyright{left:0;top:1120px;width:762px;height:80px;background:var(--black);color:#ddd;font-size:8.5px;text-align:center;padding-top:33px;word-spacing:2px}
</style>
</head>
<body>

<header>
  <div class="abs brand"><span class="brand-mark"></span><span class="brand-name">Dorrel</span></div>
  <div class="abs phone">
    <span class="phone-icon"><svg width="9" height="9" viewBox="0 0 24 24"><path fill="#fff" d="M6.6 10.8a15.1 15.1 0 0 0 6.6 6.6l2.2-2.2c.3-.3.7-.4 1-.2 1.1.4 2.3.6 3.6.6.6 0 1 .4 1 1V20c0 .6-.4 1-1 1A17 17 0 0 1 3 4c0-.6.4-1 1-1h3.5c.6 0 1 .4 1 1 0 1.3.2 2.5.6 3.6.1.3 0 .7-.2 1z"/></svg></span>
    615.555.0178
  </div>
  <div class="abs search">Search...
    <svg width="11" height="11" viewBox="0 0 24 24"><circle cx="10" cy="10" r="7" fill="none" stroke="#555" stroke-width="3"/><path d="M15 15l7 7" stroke="#555" stroke-width="3"/></svg>
  </div>
</header>

<nav class="abs nav">
  <span class="nav-item home">Home</span>
  <span class="nav-item" style="left:60px">Properties for Sale</span>
  <span class="nav-sep" style="left:170px"></span>
  <span class="nav-item" style="left:182px">Auctions
    <svg width="7" height="7" viewBox="0 0 10 10" style="margin-left:2px"><path d="M1 1l4 3 4-3M1 5l4 3 4-3" fill="none" stroke="#fff" stroke-width="1.4"/></svg>
  </span>
  <span class="nav-sep" style="left:246px"></span>
  <span class="nav-item" style="left:259px">Sell Your Property</span>
  <span class="nav-sep" style="left:366px"></span>
  <span class="nav-item" style="left:379px">Community Info</span>
  <span class="nav-sep" style="left:473px"></span>
  <span class="nav-item" style="left:486px">About Us</span>
  <span class="nav-sep" style="left:545px"></span>
  <span class="nav-item" style="left:558px">Contact Us</span>
</nav>

<section>
  <div class="abs hero" role="img" aria-label="Slideshow photo of a craftsman-style family home with white porch and green lawn"></div>
  <div class="abs dropdown">Upcoming<br>Past</div>
  <div class="abs hero-caption">WELCOME TO DORREL COMMERCIAL REALTORS<br>AUCTIONEERS LLC</div>
  <div class="abs hero-dots"><span></span><span class="on"></span><span></span><span></span></div>
</section>

<section>
  <div class="abs featured"></div>
  <h2 class="abs section-title-red" style="font-weight:400">Featured Properties</h2>
  <div class="abs feat-dots"><span></span><span class="on"></span><span></span></div>
  <div class="abs feat-photo" style="left:74px;background:linear-gradient(180deg,#6fa0d8,#8a5a3a 60%,#5d8a3c)" role="img" aria-label="Modern wood-clad house"></div>
  <div class="abs feat-photo" style="left:229px;background:linear-gradient(180deg,#c9d3da,#8d8a7e 55%,#6b6a60)" role="img" aria-label="Two-storey house under construction"></div>
  <div class="abs feat-photo" style="left:385px;background:linear-gradient(180deg,#5f9ad6,#d7c29a 55%,#5c8c3a)" role="img" aria-label="Large suburban home with flowers"></div>
  <div class="abs feat-photo" style="left:541px;background:linear-gradient(180deg,#a9c6e4,#6f7068 55%,#5e7e46)" role="img" aria-label="Grey two-storey house"></div>
  <p class="abs feat-caption" style="left:78px">Lorem Ipsum is simply</p>
  <p class="abs feat-caption" style="left:231px">Lorem Ipsum is simply</p>
  <p class="abs feat-caption" style="left:389px">Lorem Ipsum is simply</p>
  <p class="abs feat-caption" style="left:541px">Lorem Ipsum is simply</p>
</section>

<section>
  <h2 class="abs section-title" style="left:63px;top:584px">Upcoming Auctions</h2>
  <div class="abs arrows">
    <span><svg width="6" height="8" viewBox="0 0 6 8"><path d="M5 0L1 4l4 4" fill="none" stroke="#fff"/></svg></span>
    <span><svg width="6" height="8" viewBox="0 0 6 8"><path d="M1 0l4 4-4 4" fill="none" stroke="#fff"/></svg></span>
  </div>

  <article class="abs auction-card" style="top:614px">
    <div class="abs auction-photo" style="background:linear-gradient(180deg,#9bbbd6,#6d6a5e 45%,#6f9a3e 75%,#8cbc4a)" role="img" aria-label="Brick ranch house with front lawn"></div>
    <h3 class="abs auction-title">Online Bidding Only</h3>
    <p class="abs auction-lines">Begins:&nbsp; Tuesday, May 30, 2017 at 11:00 AM EDT<br>Ends:&nbsp; Wednesday, May 31, 2017 at 11:00 AM EDT<br>Live Off-Site Auction<br>Begins:&nbsp; Tuesday, May 29, 2018 at 4:00 PM EDT</p>
    <span class="abs btn-details">DETAILS</span>
  </article>

  <article class="abs auction-card" style="top:760px">
    <div class="abs auction-photo" style="background:linear-gradient(180deg,#5f8a4e,#a8633a 40%,#8a4e2a 60%,#7ea243)" role="img" aria-label="Log cabin with wraparound porch"></div>
    <h3 class="abs auction-title">Online Bidding Only</h3>
    <p class="abs auction-lines">Begins:&nbsp; Tuesday, May 30, 2017 at 11:00 AM EDT<br>Ends:&nbsp; Wednesday, May 31, 2017 at 11:00 AM EDT<br>Live Off-Site Auction<br>Begins:&nbsp; Tuesday, May 29, 2018 at 4:00 PM EDT</p>
    <span class="abs btn-details">DETAILS</span>
  </article>
</section>

<aside>
  <h2 class="abs section-title" style="left:483px;top:584px">News &amp; Events blog</h2>

  <div class="abs news-photo" style="top:619px;background:linear-gradient(180deg,#a9c5de,#b9aa94 55%,#6b9a48)" role="img" aria-label="Large stone house"></div>
  <div class="abs news-text" style="top:617px">Lorem Ipsum is simply dummy text of the printing and typesetting industry. standard dummy text<div class="news-date">25/SEP/2014</div></div>
  <div class="abs news-sep" style="top:678px"></div>

  <div class="abs news-photo" style="top:690px;background:linear-gradient(180deg,#d6c9a8,#9a7a52 55%,#6e5a3e)" role="img" aria-label="Two-storey townhouse"></div>
  <div class="abs news-text" style="top:690px">Lorem Ipsum is simply dummy text of the printing and typesetting industry. standard dummy text<div class="news-date">25/SEP/2014</div></div>
  <div class="abs news-sep" style="top:752px"></div>

  <div class="abs news-photo" style="top:766px;background:linear-gradient(180deg,#e4e6e2,#c9c4b0 50%,#7aae4a)" role="img" aria-label="White cottage with garden"></div>
  <div class="abs news-text" style="top:766px">Lorem Ipsum is simply dummy text of the printing and typesetting industry. standard dummy text<div class="news-date">25/SEP/2014</div></div>
  <div class="abs news-sep" style="top:830px"></div>

  <div class="abs news-photo" style="top:843px;background:linear-gradient(180deg,#b7cbe0,#9c9a90 50%,#5e8a3a)" role="img" aria-label="Grey family home with lawn"></div>
  <div class="abs news-text" style="top:842px">Lorem Ipsum is simply dummy text of the printing and typesetting industry. standard dummy text<div class="news-date">25/SEP/2014</div></div>
</aside>

<footer>
  <div class="abs footer-band"></div>
  <h4 class="abs footer-head" style="left:62px;font-weight:400">CONTACT INFO</h4>
  <h4 class="abs footer-head" style="left:245px;font-weight:400">TESTIMONIALS</h4>
  <h4 class="abs footer-head" style="left:545px;font-weight:400">SUBSCRIBE TO OUR NEWSLETTER</h4>

  <p class="abs contact-lines">Address: 22-C Elmfield Court W, Mur-<br>freesboro, TN 37199<br><span style="display:block;height:5px"></span>Phone: (615) 555-0178<br>Contacts: Marion Teague-Hollis<br>Email: marketing@kenwoodorrel.example</p>

  <div class="abs testimonial">
    <div class="abs avatar" role="img" aria-label="Client portrait"></div>
    <p class="abs quote"><b>“</b> Lorem Ipsum is simply dummy text of the printing and typesetting industry Lorem Ipsum has been the industry's standard dummy text <b>”</b></p>
  </div>

  <div class="abs newsletter">Enter Your Mail Id<span class="abs go">GO</span></div>
  <div class="abs social" aria-label="Social media links"><span style="background:#2aa3d8"></span><span style="background:#2f5faa"></span><span style="background:#555"></span><span style="background:#d04a86"></span></div>

  <div class="abs badges-band"></div>
  <div class="abs badges" aria-label="Association memberships">
    <span class="badge" style="width:40px"></span>
    <span class="badge" style="width:40px;height:28px"></span>
    <span class="badge" style="width:30px;height:22px;border-radius:50%"></span>
    <span class="badge" style="width:30px;border-radius:0 0 15px 15px;background:#2f5faa"></span>
    <span class="badge" style="width:44px;height:16px;border-radius:50%"></span>
    <span class="badge" style="width:34px;border-radius:50%;background:#fff;border:2px solid #3a3a3a"></span>
    <span class="badge" style="width:62px;height:28px"></span>
    <span class="badge" style="width:32px"></span>
  </div>

  <p class="abs copyright">© Copyright 2014 &nbsp;&nbsp; All Rights Reserved</p>
</footer>

</body>
</html>
```